Structural Engineering Business Card

Brookvane Drafting does residential house plans for clients in Central Florida. Would like simple but elegant business card that is appropriate for a house plan engineering company. Prefer black business card with black/white them but open to other shades of blue. I uploaded a sample card that I came across that looked good but please come up with your own creative designs.

Contact Information for Business Card

Name, Title, Phone, Email, Address, website

```html
<!DOCTYPE html>
<html lang="en">
<head>
<meta charset="utf-8">
<title>Brookvane Drafting – Business Card</title>
<link href="https://fonts.googleapis.com/css2?family=Lato:wght@400;700;900&display=swap" rel="stylesheet">
<style>
  :root{
    --stage:#1a1a1a;
    --card:#141414;
    --card-edge:#262626;
    --ink:#ffffff;
    --ink-soft:#d6d6d6;
    --rule:#9a9a9a;
    --drawing-glow:rgba(255,255,255,.07);
    --drawing-fade:rgba(255,255,255,0);
  }
  *{margin:0;padding:0;box-sizing:border-box}
  html,body{width:1200px;height:801px;overflow:hidden}
  body{
    background:var(--stage);
    font-family:"Lato",sans-serif;
    color:var(--ink);
    position:relative;
  }
  .card{
    position:absolute;
    top:252px;
    width:520px;height:297px;
    background:var(--card);
    border:1px solid var(--card-edge);
    border-radius:16px;
    overflow:hidden;
    box-shadow:0 14px 30px rgba(0,0,0,.45);
  }
  .card--front{left:50px}
  .card--back{left:630px}
  .blueprint-art{
    position:absolute;
    inset:0;
  }
  .card--front .blueprint-art{
    background:
      radial-gradient(ellipse 55% 70% at 68% 45%, var(--drawing-glow), var(--drawing-fade) 70%),
      linear-gradient(160deg,#1c1c1c,#121212);
  }
  .card--back .blueprint-art{
    background:
      radial-gradient(ellipse 45% 55% at 55% 62%, var(--drawing-glow), var(--drawing-fade) 70%),
      linear-gradient(160deg,#1c1c1c,#121212);
  }
  .wordmark{
    position:absolute;
    font-weight:900;
    color:var(--ink);
    text-transform:uppercase;
    letter-spacing:.5px;
    white-space:nowrap;
  }
  .card--front .wordmark{left:0;right:0;top:120px;text-align:center;font-size:38px}
  .card--back .wordmark{right:28px;top:32px;font-size:20px}
  .rule{position:absolute;height:1px;background:var(--rule)}
  .rule--top{left:200px;right:28px;top:78px}
  .rule--mid{left:28px;width:230px;top:214px}
  .address{
    position:absolute;right:28px;top:96px;
    text-align:right;font-size:12px;line-height:1.45;color:var(--ink-soft);
  }
  .address strong{font-weight:700;color:var(--ink)}
  .person{position:absolute;left:28px;top:156px}
  .person__name{font-size:22px;font-weight:700;text-transform:uppercase;letter-spacing:.5px}
  .person__title{font-size:13px;color:var(--ink-soft);margin-top:2px}
  .contacts{position:absolute;left:28px;top:224px;list-style:none;font-size:12px;color:var(--ink-soft)}
  .contacts li{display:flex;align-items:center;gap:8px;height:20px}
  .contacts .phone{font-size:15px;color:var(--ink)}
  .contacts svg{width:11px;height:11px;fill:var(--ink);flex:none}
</style>
</head>
<body>

<section class="card card--front" aria-label="Card front">
  <div class="blueprint-art" role="img" aria-label="Faint architectural house elevation drawing over a grid"></div>
  <div class="wordmark">Brookvane Drafting</div>
</section>

<section class="card card--back" aria-label="Card back">
  <div class="blueprint-art" role="img" aria-label="Faint architectural house elevation drawing over a grid"></div>
  <div class="wordmark">Brookvane Drafting</div>
  <div class="rule rule--top"></div>
  <p class="address"><strong>Brookvane Drafting Group</strong><br>Your Address, City<br>State, Zip 1235</p>
  <div class="person">
    <h1 class="person__name">Daniel Hart</h1>
    <p class="person__title">Founder &amp; CEO</p>
  </div>
  <div class="rule rule--mid"></div>
  <ul class="contacts">
    <li class="phone">
      <svg viewBox="0 0 24 24"><path d="M6.6 10.8a15 15 0 0 0 6.6 6.6l2.2-2.2a1 1 0 0 1 1-.25 11.4 11.4 0 0 0 3.6.57 1 1 0 0 1 1 1V20a1 1 0 0 1-1 1A17 17 0 0 1 3 4a1 1 0 0 1 1-1h3.5a1 1 0 0 1 1 1c0 1.25.2 2.45.57 3.57a1 1 0 0 1-.25 1z"/></svg>
      (123) 456-7890
    </li>
    <li>
      <svg viewBox="0 0 24 24"><path d="M2 5h20v14H2z M2 5l10 8 10-8" fill="none" stroke="#fff" stroke-width="2"/></svg>
      office@brookvane.com
    </li>
    <li>
      <svg viewBox="0 0 24 24"><circle cx="12" cy="12" r="9" fill="none" stroke="#fff" stroke-width="2"/><path d="M3 12h18M12 3c3 3 3 15 0 18M12 3c-3 3-3 15 0 18" fill="none" stroke="#fff" stroke-width="1.5"/></svg>
      www.brookvane.com
    </li>
  </ul>
</section>

</body>
</html>
```